Business Card Design for Property Development Company Director

I am looking for a professional and unforgettable business card design for our Director of our Property Development Company.
Please see attached .pptx file to find out what information to include. You don't have to follow the exact format shown in the file - I am interested to see your creative flair using the information provided.

```html
<!DOCTYPE html>
<html lang="en">
<head>
<meta charset="UTF-8">
<title>Harwell Property Group – Business Card</title>
<link href="https://fonts.googleapis.com/css2?family=Montserrat:wght@400;500;600;700&family=Open+Sans:wght@400&display=swap" rel="stylesheet">
<style>
  :root {
    --backdrop: #3a3a3a;
    --card: #ffffff;
    --brand-blue: #2f55a4;
    --ink-grey: #5b5b5b;
    --mark-grey: #58595b;
  }
  * { margin: 0; padding: 0; box-sizing: border-box; }
  html, body { width: 1200px; height: 800px; overflow: hidden; }
  body { background: var(--backdrop); position: relative; font-family: "Montserrat", sans-serif; }

  .card {
    position: absolute; left: 316px; width: 570px; height: 330px;
    background: var(--card);
    box-shadow: 0 10px 18px rgba(0,0,0,0.45);
  }
  .card--front { top: 51px; }
  .card--back { top: 418px; }

  /* Front */
  .tagline {
    position: absolute; top: 64px; left: 0; width: 100%;
    text-align: center; font-family: "Open Sans", sans-serif;
    color: var(--brand-blue); font-size: 17.5px; line-height: 28px;
  }
  .brand {
    position: absolute; display: flex; align-items: center;
  }
  .brand__square { background: var(--mark-grey); flex: none; }
  .brand__name {
    font-family: "Montserrat", sans-serif; font-weight: 700;
    color: var(--brand-blue); text-transform: uppercase; line-height: 1.05;
    white-space: nowrap;
  }
  .card--front .brand { top: 155px; left: 140px; }
  .card--front .brand__square { width: 62px; height: 62px; margin-right: 20px; }
  .card--front .brand__name { font-size: 27px; letter-spacing: 1px; }

  .invite {
    position: absolute; top: 280px; left: 0; width: 100%;
    text-align: center; font-family: "Open Sans", sans-serif;
    color: var(--ink-grey); font-size: 14px;
  }

  /* Back */
  .card--back .brand { top: 143px; left: 58px; }
  .card--back .brand__square { width: 44px; height: 44px; margin-right: 12px; }
  .card--back .brand__name { font-size: 14px; letter-spacing: 0.4px; line-height: 1.2; }

  .divider {
    position: absolute; left: 284px; top: 112px; width: 1.5px; height: 105px;
    background: var(--brand-blue);
  }
  .contact { position: absolute; left: 305px; top: 108px; }
  .contact__name { color: var(--brand-blue); font-size: 16.5px; font-weight: 500; letter-spacing: 0.3px; }
  .contact__role { color: var(--ink-grey); font-size: 16.5px; font-weight: 500; margin-top: 5px; }
  .contact__list { list-style: none; margin-top: 8px; }
  .contact__item {
    display: flex; align-items: center; color: var(--ink-grey);
    font-size: 14.5px; font-weight: 500; height: 20.5px;
  }
  .contact__icon { width: 11px; height: 11px; margin-right: 7px; flex: none; }

  .licence {
    position: absolute; top: 288px; left: 0; width: 100%;
    text-align: center; color: var(--ink-grey); font-size: 13.5px; font-weight: 500;
  }
</style>
</head>
<body>
  <section class="card card--front">
    <p class="tagline">Property Development &amp;<br>Site Acquisition Specialists</p>
    <div class="brand">
      <span class="brand__square"></span>
      <span class="brand__name">Harwell<br>Property Group</span>
    </div>
    <p class="invite">Ask me about our INVESTMENT &amp; PARTNERSHIP opportunities</p>
  </section>

  <section class="card card--back">
    <div class="brand">
      <span class="brand__square"></span>
      <span class="brand__name">Harwell<br>Property Group</span>
    </div>
    <div class="divider"></div>
    <div class="contact">
      <p class="contact__name">DANIEL MARSH</p>
      <p class="contact__role">Director</p>
      <ul class="contact__list">
        <li class="contact__item">
          <svg class="contact__icon" viewBox="0 0 12 12"><path d="M2.5 1 L4.5 1 L5.2 3.5 L4 4.5 C4.6 6 6 7.4 7.5 8 L8.5 6.8 L11 7.5 L11 9.5 C11 10.4 10.3 11 9.5 11 C5 10.7 1.3 7 1 2.5 C1 1.7 1.6 1 2.5 1 Z" fill="var(--brand-blue)"/></svg>
          0400 123 456
        </li>
        <li class="contact__item">
          <svg class="contact__icon" viewBox="0 0 12 12"><rect x="0.8" y="2" width="10.4" height="8" fill="none" stroke="var(--brand-blue)" stroke-width="1.6"/><path d="M1 2.5 L6 6.5 L11 2.5" fill="none" stroke="var(--brand-blue)" stroke-width="1.4"/></svg>
          daniel@harwellgroup.com.au
        </li>
        <li class="contact__item">
          <svg class="contact__icon" viewBox="0 0 12 12"><circle cx="6" cy="6" r="5.2" fill="var(--brand-blue)"/><path d="M3 3.5 Q5 4 4.5 6 Q6 7 5 9.5 M8 2.5 Q7 4.5 9 5.5" fill="none" stroke="#fff" stroke-width="1"/></svg>
          www.harwellgroup.com.au
        </li>
      </ul>
    </div>
    <p class="licence">Real Estate Lic: 1234567 &amp; 1234568</p>
  </section>
</body>
</html>
```